Business card for law firm

Need business card for new law firm. Think confident, authoritative, conservative, but not stuffy or old-fashioned.

Contact Information for Business Card

Content for card - logo (uploaded), plus the following:

Paul Whitcombe (larger font)
Managing Partner (larger font, but not as large as name)
Level 9, 7 Ferris Lane
Sydney NSW 2000
Main Tel 02 9364 2710
Direct Tel 02 8472 3159
Email paul@qvlegal.com.au
www.qvlegal.com.au

Letterhead design should include logo plus:
Level 9, 7 Ferris Lane
Sydney NSW 2000
Tel 02 8472 3159
www.qvlegal.com.au

```html
<!DOCTYPE html>
<html lang="en">
<head>
<meta charset="utf-8">
<title>Quayvale Legal — Business Card</title>
<link rel="stylesheet" href="https://fonts.googleapis.com/css2?family=Montserrat:wght@700&family=Jost:wght@400;500&display=swap">
<style>
  :root {
    --backdrop: #3a3a3c;
    --card-white: #ffffff;
    --card-dark: #3b3b3d;
    --card-dark-band: #1c1c1d;
    --navy: #1b2a5e;
    --ink: #1a1a1a;
    --ink-soft: #3c3c3c;
    --emboss: #2a2a2b;
  }
  * { box-sizing: border-box; margin: 0; padding: 0; }
  html, body {
    width: 1200px;
    height: 1000px;
    overflow: hidden;
    background: var(--backdrop);
  }
  .stage {
    position: relative;
    width: 1200px;
    height: 1000px;
  }
  .card {
    position: absolute;
    width: 700px;
    height: 400px;
    border-radius: 28px;
    overflow: hidden;
  }

  /* Reverse side */
  .card--reverse {
    left: 430px;
    top: 60px;
    background: var(--card-dark);
  }
  .reverse-band {
    position: absolute;
    left: 0; top: 0;
    width: 200px; height: 100%;
    background: var(--card-dark-band);
  }
  .reverse-wordmark {
    position: absolute;
    left: 290px; top: 150px;
    display: flex; align-items: center; gap: 14px;
    font-family: "Jost", sans-serif;
    font-weight: 500;
    font-size: 38px;
    letter-spacing: 4px;
    color: var(--emboss);
  }
  .reverse-wordmark .mark-square {
    width: 30px; height: 30px;
    background: var(--emboss);
  }
  .reverse-web {
    position: absolute;
    left: 390px; top: 290px;
    font-family: "Jost", sans-serif;
    font-weight: 500;
    font-size: 17px;
    color: var(--emboss);
  }

  /* Front side */
  .card--front {
    left: 90px;
    top: 520px;
    background: var(--card-white);
  }
  .contact {
    position: absolute;
    left: 40px; top: 34px;
    font-family: "Jost", sans-serif;
    color: var(--ink-soft);
    font-size: 17px;
    line-height: 1.35;
  }
  .contact__name {
    font-family: "Montserrat", sans-serif;
    font-weight: 700;
    font-size: 24px;
    color: var(--navy);
    text-transform: uppercase;
    line-height: 1.2;
  }
  .contact__role { font-size: 19px; margin-bottom: 2px; }
  .contact__label { color: var(--navy); font-weight: 500; }
  .contact__sep { margin: 0 4px; }

  .front-brand {
    position: absolute;
    right: 40px; bottom: 90px;
    display: flex; align-items: center; gap: 14px;
    font-family: "Jost", sans-serif;
    font-weight: 500;
    font-size: 36px;
    letter-spacing: 4px;
    color: var(--navy);
  }
  .front-brand .mark-square {
    width: 30px; height: 30px;
    background: var(--navy);
  }
  .front-address {
    position: absolute;
    right: 40px; bottom: 44px;
    font-family: "Jost", sans-serif;
    font-weight: 500;
    font-size: 18px;
    color: var(--ink);
  }
</style>
</head>
<body>
<main class="stage">
  <section class="card card--reverse">
    <div class="reverse-band"></div>
    <div class="reverse-wordmark"><span class="mark-square"></span>QUAYVALE LEGAL</div>
    <div class="reverse-web">www.qvlegal.com.au</div>
  </section>

  <section class="card card--front">
    <div class="contact">
      <div class="contact__name">Paul Whitcombe</div>
      <div class="contact__role">Managing Partner</div>
      <div><span class="contact__label">Main Tel</span> 02 9364 2710<span class="contact__sep">|</span><span class="contact__label">Direct Tel</span> 02 8472 3159</div>
      <div><span class="contact__label">E:</span> paul@qvlegal.com.au<span class="contact__sep">|</span><span class="contact__label">W:</span> www.qvlegal.com</div>
    </div>
    <div class="front-brand"><span class="mark-square"></span>QUAYVALE LEGAL</div>
    <div class="front-address">Level 9, 7 Ferris Lane Sydney NSW 2000</div>
  </section>
</main>
</body>
</html>
```